Wesbite design for Investment Firm

We want a basic (clean) website that follows the form, fonts and colors of our attachments. This is for a financial investment management firm, but we have a boutique (anti-Wall Street) approach. Site should have an Home Page (Logo up top - room for basic copy on bottom, Philosophy Page (room for Quarterly Letter attachment and basic copy, Performance Page (room for Performance Overview and Performance Analysis and basic copy), Team Page, Commentary Page and Contact

Reason: Some designers have asked for an extension. Again, please only use image of Train Station or Train Station Logo in design.

Target Market(s)

Small and mid-size financial advisors from across the country

Industry/Entity Type

Financial

Number of Pages Required

5+ page

Font styles to use
Other font styles liked:
• Palotino Linotype

Colors
3176b5
cfdeed
ffffff

Requirements
Must have
• Please refer to existing site www.qlvor.example. Of note, this is too complex / cluttered. We simply want Blur, Grey and White consistent with attachments. The copy is pretty good, but will be simplified (and no quotes)
Should not have
• No images other than train station logo and / or train station image

```html
<!DOCTYPE html>
<html lang="en">
<head>
<meta charset="utf-8">
<title>Aldergate Investment Company</title>
<link href="https://fonts.googleapis.com/css2?family=Crimson+Text:wght@400;600&family=Open+Sans:ital,wght@0,300;0,400;0,600;0,700;1,300&display=swap" rel="stylesheet">
<style>
:root{
  --blue:#3176b5;
  --blue-soft:#cfdeed;
  --white:#ffffff;
  --grey-bg:#f3f3f3;
  --text:#555b61;
  --dark:#2d3136;
  --muted:#9a9ea3;
  --rule:#e1e4e8;
}
*{box-sizing:border-box;margin:0;padding:0}
html,body{width:669px;height:1200px;overflow:hidden;background:var(--white)}
body{font-family:"Open Sans",Arial,sans-serif;color:var(--text);position:relative}
.site-header{height:60px;text-align:center;padding-top:10px}
.brand-name{font-family:"Crimson Text",Georgia,serif;font-size:25px;color:var(--blue);line-height:1;font-weight:400}
.brand-tag{font-family:"Crimson Text",Georgia,serif;font-size:12px;color:var(--muted);line-height:1.1}
.main-nav{height:27px;background:var(--blue);display:flex;justify-content:center;align-items:center;gap:0}
.main-nav a{color:var(--white);text-decoration:none;font-size:8px;font-weight:600;letter-spacing:.2px;padding:0 16px}
.main-nav a.active{color:var(--blue-soft)}
.hero{position:relative;height:281px;overflow:hidden}
.hero-photo{position:absolute;inset:0;background:linear-gradient(160deg,#6d8fb5 0%,#9aa7b3 25%,#6b5e52 45%,#d9dade 60%,#c9ccd1 78%,#4b4f3d 100%)}
.hero-curve{position:absolute;left:0;bottom:0;width:669px;height:22px}
.hero-text{position:absolute;top:172px;left:0;right:0;text-align:center;color:var(--white)}
.hero-title{font-size:38px;font-weight:400;line-height:1;text-shadow:0 1px 3px rgba(0,0,0,.35)}
.hero-sub{font-size:8.5px;margin-top:8px;text-shadow:0 1px 2px rgba(0,0,0,.5)}
.hero-arrow{position:absolute;top:212px;width:10px;height:20px}
.welcome{height:188px;text-align:center;padding:24px 80px 0}
.welcome h1{font-size:21px;font-weight:400;color:var(--blue);margin-bottom:18px}
.welcome p{font-size:8.5px;line-height:13px;margin-bottom:12px}
.philosophy{position:relative;height:234px;text-align:center;color:var(--white);padding:34px 78px 0;overflow:hidden}
.philosophy-photo{position:absolute;inset:0;background:radial-gradient(ellipse at 75% 55%,#3e6fa6 0%,#4c82c0 35%,#5a8fcc 70%,#6b9bd2 100%)}
.philosophy-content{position:relative}
.philosophy h2{font-size:23px;font-weight:300;letter-spacing:.5px;margin-bottom:12px}
.philosophy p{font-size:8.3px;line-height:13.5px;margin-bottom:8px}
.btn-outline{display:inline-block;margin-top:17px;width:126px;height:29px;line-height:27px;border:1px solid var(--white);color:var(--white);font-size:10px;font-weight:600;text-decoration:none}
.testimonials{position:relative;height:237px;background:var(--grey-bg);text-align:center;padding-top:34px}
.testimonials h2{font-size:18px;font-weight:300;color:var(--dark);margin-bottom:14px}
.quote{font-size:11px;font-style:italic;font-weight:300;line-height:16px;color:var(--dark);width:400px;margin:0 auto}
.quote-mark{position:absolute;font-family:Georgia,serif;font-size:34px;color:#dcdcdc;line-height:1}
.avatar-ring{width:70px;height:70px;border-radius:50%;background:var(--white);border:1px solid #e2e2e2;margin:11px auto 0;display:flex;align-items:center;justify-content:center}
.avatar{width:62px;height:62px;border-radius:50%;background:linear-gradient(#bdbdbd,#8f8f8f)}
.author{font-size:8.5px;letter-spacing:1px;color:var(--dark);margin-top:8px}
.side-arrow{position:absolute;top:305px;width:10px;height:20px}
.site-footer{height:140px;display:flex;padding-top:22px}
.footer-col{border-right:1px solid var(--rule);height:88px;padding:0 16px}
.footer-col:last-child{border-right:none}
.footer-col h3{font-size:10px;font-weight:400;color:var(--blue);margin-bottom:8px}
.letter{width:161px;text-align:center}
.letter-caption{font-size:6px;color:var(--blue-soft);margin-bottom:3px}
.letter-thumb{width:53px;height:69px;margin:0 auto;border:1px solid #9a9a9a;background:linear-gradient(#fafafa,#ececec)}
.commentary{width:187px}
.post-title{font-size:7px;color:var(--dark)}
.post-date{font-size:6.5px;color:var(--muted);margin-bottom:6px}
.post-excerpt{font-size:5.8px;line-height:8px;color:var(--dark)}
.read-more{font-size:5.8px;color:var(--blue)}
.links{width:148px;padding-left:34px}
.links ul{list-style:none}
.links li{font-size:7px;color:var(--dark);margin-bottom:8px}
.contact{padding-left:34px}
.contact p{font-size:7px;color:var(--dark);line-height:11px;display:flex;gap:3px}
.contact svg{flex:none;margin-top:2px}
.bottom-bar{position:absolute;left:0;bottom:0;width:669px;height:33px;background:var(--blue);color:var(--white);font-size:7px;text-align:center;line-height:33px}
</style>
</head>
<body>
<header class="site-header">
  <div class="brand-name">Aldergate Investment Company</div>
  <div class="brand-tag">Separately Managed Accounts</div>
</header>
<nav class="main-nav">
  <a class="active" href="#">HOME</a><a href="#">PHILOSOPHY</a><a href="#">PERFORMANCE</a><a href="#">TEAM</a><a href="#">LETTERS</a><a href="#">COMMENTARY</a><a href="#">CONTACT</a>
</nav>
<section class="hero">
  <div class="hero-photo" role="img" aria-label="Photograph of a white clapboard train station with a shingled roof"></div>
  <svg class="hero-arrow" style="left:20px" viewBox="0 0 10 20"><polyline points="9,1 1,10 9,19" fill="none" stroke="#fff" stroke-width="1"/></svg>
  <svg class="hero-arrow" style="right:20px" viewBox="0 0 10 20"><polyline points="1,1 9,10 1,19" fill="none" stroke="#fff" stroke-width="1"/></svg>
  <div class="hero-text">
    <div class="hero-title">Aldergate Investment Company</div>
    <div class="hero-sub">The high expectations of our original investors is a key contributor to our value driven investment philosophy.</div>
  </div>
  <svg class="hero-curve" viewBox="0 0 669 22" preserveAspectRatio="none"><path d="M0 22 Q334 -20 669 22 Z" fill="#fff"/></svg>
</section>
<section class="welcome">
  <h1>Welcome to Aldergate Investment Company</h1>
  <p>We founded Aldergate Investment Company in 1999, initially managing wealth from our family and friends in the town of Aldergate. The high expectations of our original investors is a key contributor to our value driven investment philosophy.</p>
  <p>Based in Dallas, TX, we manage assets for both individuals and institutions. Our investment methodology stresses absolute returns vs. relative performance, blending a combination of fundamental analysis, discipline and patience with the goal of preserving and compounding capital.</p>
</section>
<section class="philosophy">
  <div class="philosophy-photo" role="img" aria-label="Blurred blue-toned photograph of a man on the phone by an office window"></div>
  <div class="philosophy-content">
    <h2>OUR PHILOSOPHY</h2>
    <p>Our proprietary investment research seeks to determine the appraised value of a company. Investments are then made at a significant discount, ideally 20% to 40% below the company's current intrinsic value. This approach allows us to buy companies with a sufficient margin of safety, as valuations are imprecise and the future is unpredictable.</p>
    <p>Our process demands that we not trade stocks, but rather consider businesses we would like and purchase and hold for 5 to 10 years. We therefore mitigate risk via a thorough examination and understanding of each business we fractionally own.</p>
    <a class="btn-outline" href="#">LEARN MORE</a>
  </div>
</section>
<section class="testimonials">
  <h2>Clients Testimonials</h2>
  <span class="quote-mark" style="left:113px;top:72px">&ldquo;</span>
  <p class="quote">"The stock market is filled with individuals who know the price of everything, but the value of nothing."</p>
  <span class="quote-mark" style="left:528px;top:96px">&rdquo;</span>
  <div class="avatar-ring"><div class="avatar" role="img" aria-label="Portrait photograph of the quoted author"></div></div>
  <div class="author">– HAROLD WINSLOW</div>
  <svg class="side-arrow" style="left:56px;top:93px" viewBox="0 0 10 20"><polyline points="9,1 1,10 9,19" fill="none" stroke="#bbb" stroke-width="1"/></svg>
  <svg class="side-arrow" style="right:56px;top:93px" viewBox="0 0 10 20"><polyline points="1,1 9,10 1,19" fill="none" stroke="#bbb" stroke-width="1"/></svg>
</section>
<footer class="site-footer">
  <div class="footer-col letter">
    <div class="letter-caption">Investment Adviser's Letter</div>
    <div class="letter-thumb" role="img" aria-label="Cover of the quarterly investment adviser's letter"></div>
  </div>
  <div class="footer-col commentary">
    <h3>LATEST COMMENTARY</h3>
    <div class="post-title">Core Equity Portfolio – Q2 2017</div>
    <div class="post-date">August 10, 2017</div>
    <div class="post-excerpt">Based on our estimate of fair value relative to the company's current stock price, we determine each company's current margin of safety in the Core Equity ...</div>
    <a class="read-more" href="#">CONTINUE READING</a>
  </div>
  <div class="footer-col links">
    <h3>QUICK LINKS</h3>
    <ul>
      <li>› Performance Overview</li>
      <li>› Performance Analysis</li>
      <li>› Verification Statement</li>
      <li>› Aldergate ADV Part 2</li>
    </ul>
  </div>
  <div class="footer-col contact">
    <h3>CONTACT US</h3>
    <p><svg width="6" height="8" viewBox="0 0 6 8"><path d="M3 0a3 3 0 0 0-3 3c0 2 3 5 3 5s3-3 3-5a3 3 0 0 0-3-3z" fill="#2d3136"/></svg><span>1520 Cedar Row Avenue,<br>Suite 210<br>Dallas, TX 75000</span></p>
    <p style="margin-top:2px"><svg width="7" height="7" viewBox="0 0 7 7"><path d="M1 0h1.5l.8 1.8-1 .8a4 4 0 0 0 2.1 2.1l.8-1 1.8.8V6a1 1 0 0 1-1 1A6 6 0 0 1 0 1a1 1 0 0 1 1-1z" fill="#2d3136"/></svg><span>214.555.0182</span></p>
    <p><svg width="8" height="6" viewBox="0 0 8 6"><rect x=".5" y=".5" width="7" height="5" fill="none" stroke="#2d3136"/><polyline points=".5,.5 4,3.5 7.5,.5" fill="none" stroke="#2d3136"/></svg><span>info@qlvor.example</span></p>
  </div>
</footer>
<div class="bottom-bar">Copyrights © 2017 Aldergate Investment Company. All Rights Reserved.</div>
</body>
</html>
```